Migration and redesign of existing website to WordPress using DIVI 3

I. TASK OBJECTIVE:
- Redesign our existing website www.kelvaleheelcare.com.au with a fresh new look and migrate to new Wordpress site based on DIVI3 theme. The site will contain the same basic functionality as the existing site (with some small changes).

II. STYLE/ DESIGN ASPECT:
As an example of a site that I like the look of, see https://pebblequarn.com/. I like the use of shadows, and this would go well with the little animations you can do with Divi (e.g. when hovering over pics).

1. What I am looking for is a design which has lots of white space, is modern and friendly looking (but still not too cute or frivolous, as we are a medical practice)
2. DESIGN that is NOT TOO rectangular or blocky.
3. Please take into consideration our Users are Older market, so any icons or navigation features need to be very easy to understand and not too small.
4. Must be easy to navigate
5. We are are happy to go with a new colour scheme, and are working on some ideas for this, but happy to take suggestions.

III. SPECIFICATIONS:
1. 5+ Pages (should flow like the current site)
2. Using Wordpress Divi 3 theme.
3. I'd like every page to have a "book now" button and a contact form in a sidebar so that users can click the button or fill in the contact form without scrolling at all. EXCEPT ON THE HOME PAGE, where there should still be a book now button (maybe on the top right in the header of all pages?), and maybe a contact us button which scrolls down to the contact area at the bottom of the HOME page. I don't think a side bar is necessarily required on the home page, but if you think it makes sense from a design perspective please let me know.
4. AT THE BOTTOM OF THE PAGE, just above the FOOTER, I'd like a row of trust logos for various organisations that we are affiliated with. (A list of this company will be provided later but you could temporarily use placeholders)

Once we have a structure in place, we can migrate most of the content. Please let me know if I'm not being clear or you need further information.

Podiatry Customers and Referrors

Health Care

5+ page

• Simple to navigate.
• Contact/booking details on most if not all pages - please see specification above
• Section for Trusted Affiliates above the footer
• Wordpress using Divi3 Theme
• Not too busy with the design. Plenty of white space or light background.
• Should not be complicated to navigate.
• TOO rectangular or blocky designs

```html
<!DOCTYPE html>
<html lang="en">
<head>
<meta charset="utf-8">
<title>Kelvale Heel Care Clinic</title>
<link href="https://fonts.googleapis.com/css2?family=Montserrat:wght@400;500;600;700&family=Open+Sans:wght@400;600;700&display=swap" rel="stylesheet">
<style>
:root{
  --teal:#1a93bd;
  --teal-dark:#0e6f93;
  --panel:#0d6388;
  --footer:#0f4a5e;
  --orange:#f59a23;
  --ink:#2f3337;
  --muted:#7a8088;
  --partner:#3a3f44;
  --white:#ffffff;
}
*{box-sizing:border-box;margin:0;padding:0}
html,body{width:1200px;height:4368px;overflow:hidden;background:var(--white)}
body{font-family:"Open Sans",Arial,sans-serif;color:var(--ink);position:relative}
.abs{position:absolute}
h2.section-title{font-family:"Montserrat",Arial,sans-serif;font-weight:500;font-size:44px;letter-spacing:1px;color:var(--ink);text-align:center}

/* Header */
.site-header{left:0;top:0;width:1200px;height:80px;background:var(--white);z-index:5;box-shadow:0 2px 8px rgba(0,0,0,.05)}
.brand{left:116px;top:10px;display:flex;align-items:center;gap:10px}
.brand-dot{width:46px;height:46px;border-radius:50%;background:var(--teal)}
.brand-name{font-weight:600;font-size:17px;color:var(--teal-dark);line-height:1.15;width:150px}
.main-nav{left:392px;top:48px;display:flex;gap:22px;font-family:"Montserrat",Arial,sans-serif;font-size:12px;font-weight:600;color:var(--ink);letter-spacing:.3px}
.main-nav .active{color:var(--teal)}
.header-call{left:760px;top:8px;font-size:11px;color:var(--muted);line-height:1.3;display:flex;gap:8px;align-items:center}
.header-call strong{display:block;font-size:15px;color:var(--ink)}
.book-now{left:890px;top:0;width:130px;height:38px;background:var(--teal);color:var(--white);text-align:center;font-family:"Montserrat",Arial,sans-serif;font-weight:700;font-size:13px;padding-top:5px;line-height:1.2;border-radius:0 0 6px 6px}
.book-now small{display:block;font-size:8px;font-weight:500}
.header-social{left:1036px;top:8px;display:flex;gap:10px}
.header-social span{width:20px;height:20px;border-radius:50%;background:var(--teal-dark)}

/* Hero */
.hero{left:0;top:0;width:1200px;height:780px;
  background:
   radial-gradient(ellipse 260px 200px at 930px 260px,#f2e7a0 0%,rgba(242,231,160,0) 100%),
   radial-gradient(ellipse 300px 120px at 760px 520px,#3c3a3d 0%,rgba(60,58,61,0) 100%),
   radial-gradient(ellipse 180px 160px at 560px 420px,#e7b99c 0%,rgba(231,185,156,0) 100%),
   radial-gradient(ellipse 320px 420px at 420px 330px,#f7f9fa 0%,rgba(247,249,250,0) 100%),
   linear-gradient(110deg,#c9d4d8 0%,#e6ebec 35%,#ddd4c8 65%,#b9b1a5 100%)}
.hero-wave{left:0;top:600px;width:1200px;height:190px}
.hero-oval{left:110px;top:160px;width:440px;height:340px}
.hero-text{left:170px;top:236px;width:320px;text-align:center;color:var(--white);font-family:"Montserrat",Arial,sans-serif;font-weight:600;font-size:22px;line-height:1.35;letter-spacing:.4px}
.btn{display:inline-block;border-radius:22px;font-family:"Montserrat",Arial,sans-serif;font-weight:700;font-size:13px;color:var(--white);letter-spacing:.5px;text-align:center}
.hero-btn{left:266px;top:456px;width:128px;height:40px;line-height:40px;background:var(--teal-dark);box-shadow:0 4px 10px rgba(0,0,0,.2)}

/* About */
.about-title{left:112px;top:840px;font-family:"Montserrat",Arial,sans-serif;font-weight:500;font-size:44px}
.about-copy{left:112px;top:920px;width:640px;font-size:14px;line-height:1.7;color:var(--muted)}
.about-copy p+p{margin-top:14px}
.about-copy .hl{color:var(--teal)}
.about-btn{left:112px;top:1096px;width:104px;height:34px;line-height:34px;background:var(--teal);font-size:11px}
.about-brand{left:830px;top:920px;text-align:center;width:230px}
.about-brand .brand-dot{width:110px;height:110px;margin:0 auto 12px}
.about-brand .brand-name{width:auto;font-size:18px}
.about-wave{left:0;top:1180px;width:1200px;height:200px}

/* Services */
.service{top:1476px;width:220px;text-align:center}
.service-ring{width:216px;height:216px;border-radius:50%;background:var(--teal);padding:10px;margin:0 auto;box-shadow:0 10px 22px rgba(0,0,0,.18)}
.service-photo{width:196px;height:196px;border-radius:50%;border:6px solid var(--white)}
.service-label{margin-top:26px;font-family:"Montserrat",Arial,sans-serif;font-weight:600;font-size:15px;color:var(--ink)}

/* Free book */
.book-band{left:0;top:1840px;width:1200px;height:680px;background:
  radial-gradient(ellipse 380px 260px at 520px 400px,#e9d8cc 0%,rgba(233,216,204,0) 100%),
  linear-gradient(90deg,#f7f8f8 0%,#eef0f0 55%,#dfe4e6 100%)}
.book-title{left:192px;top:2020px;font-family:"Montserrat",Arial,sans-serif;font-weight:500;font-size:58px;color:var(--ink)}
.book-sub{left:196px;top:2094px;width:500px;font-family:"Montserrat",Arial,sans-serif;font-weight:600;font-size:19px;line-height:1.35}
.book-sub span{color:var(--teal)}
.book-desc{left:196px;top:2164px;width:430px;font-size:13px;line-height:1.6;color:var(--muted)}
.book-btn{left:196px;top:2234px;width:120px;height:36px;line-height:36px;background:var(--orange);font-size:11px}
.book-cover{left:782px;top:1918px;width:280px;height:500px;background:var(--white);box-shadow:14px 16px 30px rgba(0,0,0,.25)}
.cover-title{padding:28px 22px 0;font-family:"Montserrat",Arial,sans-serif;font-weight:600;font-size:26px;color:var(--teal-dark)}
.cover-author{padding:8px 22px 0;font-size:11px;color:var(--ink)}
.cover-list{padding:10px 22px 0;font-size:9px;line-height:1.6;color:var(--muted);list-style:none}
.cover-photo{position:absolute;left:0;bottom:0;width:280px;height:300px;background:linear-gradient(160deg,#9ec3d4,#4f8aa6 60%,#2f5d74)}

/* Team */
.team-title{left:0;top:2578px;width:1200px}
.team-card{top:2672px;width:218px;height:282px;background:var(--white);box-shadow:0 6px 18px rgba(0,0,0,.15)}
.team-photo{width:218px;height:210px}
.team-name{height:72px;background:var(--teal);color:var(--white);text-align:center;padding-top:14px}
.team-name b{display:block;font-family:"Montserrat",Arial,sans-serif;font-size:15px;font-weight:600;letter-spacing:.4px}
.team-name span{font-size:12px}
.team-arrow{top:2790px;width:24px;height:40px}

/* Partners */
.partners-title{left:0;top:3080px;width:1200px}
.partner{top:3182px;height:40px;display:flex;align-items:center;gap:10px}
.partner i{display:block;width:30px;height:30px;border-radius:50%;background:var(--partner)}
.partner b{display:block;height:16px;border-radius:3px;background:var(--partner)}

/* Contact footer */
.contact-wave{left:0;top:3290px;width:1200px;height:600px}
.subscribe{left:120px;top:3464px;display:flex}
.subscribe-input{width:340px;height:48px;background:#0a5a7a;color:#b9d6e3;font-size:13px;padding:15px 14px}
.subscribe-btn{width:120px;height:48px;background:#e9eef0;color:var(--ink);font-family:"Montserrat",Arial,sans-serif;font-weight:700;font-size:13px;text-align:center;line-height:48px}
.contact-title{left:120px;top:3556px;font-family:"Montserrat",Arial,sans-serif;font-weight:600;font-size:30px;color:var(--white)}
.contact-line{left:120px;color:var(--white);font-size:14px;display:flex;gap:10px;align-items:flex-start;line-height:1.4}
.contact-brand{left:160px;top:3700px;display:flex;align-items:center;gap:10px}
.contact-brand .brand-dot{width:42px;height:42px;background:var(--white)}
.contact-brand .brand-name{color:var(--white);font-size:15px}
.appt{left:592px;top:3520px;width:490px;height:340px;background:var(--panel);padding:22px 22px;box-shadow:0 8px 20px rgba(0,0,0,.2);z-index:2}
.appt h3{font-family:"Montserrat",Arial,sans-serif;font-weight:500;font-size:26px;color:var(--white);letter-spacing:.5px;white-space:nowrap}
.appt-grid{display:grid;grid-template-columns:1fr 1fr;gap:12px;margin-top:20px}
.field{height:38px;background:var(--white);font-size:12px;color:var(--muted);padding:11px 12px}
.field.area{grid-column:1/3;height:90px}
.appt-submit{grid-column:1/3;height:38px;background:#0a4d6b;color:var(--white);text-align:center;line-height:38px;font-family:"Montserrat",Arial,sans-serif;font-weight:700;font-size:13px}

/* Map */
.map{left:0;top:3872px;width:1200px;height:310px;background:linear-gradient(135deg,#e9efe4 0%,#dfe7e0 45%,#b9d3e3 75%,#a9cbe0 100%)}
.map-toggle{left:10px;top:3882px;display:flex;background:var(--white);box-shadow:0 1px 4px rgba(0,0,0,.25);font-size:12px}
.map-toggle span{padding:6px 10px}
.map-toggle span:first-child{font-weight:600}
.map-card{left:470px;top:3888px;width:260px;height:110px;background:var(--white);padding:12px 14px;font-size:12px;line-height:1.5;box-shadow:0 2px 8px rgba(0,0,0,.25)}
.map-card b{font-size:14px}

/* Footer */
.site-footer{left:0;top:4182px;width:1200px;height:186px;background:var(--footer)}
.footer-social{left:0;top:4226px;width:1200px;display:flex;justify-content:center;gap:12px}
.footer-social span{width:28px;height:28px;border-radius:50%;background:var(--white)}
.copyright{left:0;top:4278px;width:1200px;text-align:center;font-size:11px;color:#b8cdd6}
</style>
</head>
<body>

<!-- Hero -->
<div class="abs hero" role="img" aria-label="Photo of a podiatrist in a white coat examining a patient's foot in a bright clinic"></div>
<svg class="abs hero-wave" viewBox="0 0 1200 190" preserveAspectRatio="none"><path d="M0 110 C200 40 380 150 600 100 C820 50 980 20 1200 80 L1200 190 L0 190Z" fill="#ffffff"/></svg>
<svg class="abs hero-oval" viewBox="0 0 440 340"><ellipse cx="220" cy="170" rx="214" ry="160" fill="#1a93bd" fill-opacity=".82" stroke="#ffffff" stroke-opacity=".5" stroke-width="4"/></svg>
<div class="abs hero-text">WE OFFER TREATMENTS TO ALLEVIATE PAIN AND GET ATHLETES AND DANCERS BACK IN ACTION QUICKLY</div>
<a class="abs btn hero-btn">LEARN MORE</a>

<!-- Header -->
<header class="abs site-header">
  <div class="abs brand"><span class="brand-dot"></span><span class="brand-name">Kelvale Heel Care Clinic</span></div>
  <div class="abs header-call"><svg width="18" height="18" viewBox="0 0 24 24"><path d="M6.6 10.8a15 15 0 006.6 6.6l2.2-2.2a1 1 0 011-.25 11.4 11.4 0 003.6.57 1 1 0 011 1V20a1 1 0 01-1 1A17 17 0 013 4a1 1 0 011-1h3.5a1 1 0 011 1 11.4 11.4 0 00.57 3.6 1 1 0 01-.25 1z" fill="#1a93bd"/></svg><div>CALL US<strong>(08) 9000 4127</strong></div></div>
  <div class="abs book-now">BOOK NOW<small>Contact us for a booking</small></div>
  <div class="abs header-social"><span></span><span></span><span></span><span></span></div>
  <nav class="abs main-nav"><span class="active">ABOUT US</span><span>COMMON PROBLEMS</span><span>SERVICES</span><span>CASE HISTORIES</span><span>INFORMATION</span><span>BLOG</span><span>CONTACT</span></nav>
</header>

<!-- About -->
<h2 class="abs about-title">ABOUT US</h2>
<div class="abs about-copy">
  <p>The <span class="hl">Kelvale Heel Care Clinic</span> was established in 1991 by Dr Dana Whitford. We currently have six podiatrists and two administration staff members housed in a modern, state-of-the-art clinic with ample parking on site.</p>
  <p>Just like you, we want you to get better as soon as possible. That is why we focus on making your visit as informative and supportive as possible, empowering you to take control of your condition and make the best treatment choice. Ask about our specials.</p>
</div>
<a class="abs btn about-btn">VIEW MORE</a>
<div class="abs about-brand"><div class="brand-dot"></div><div class="brand-name">Kelvale Heel Care Clinic</div></div>
<svg class="abs about-wave" viewBox="0 0 1200 200" preserveAspectRatio="none"><path d="M0 60 C220 150 420 0 640 70 C860 140 1000 40 1200 90 L1200 200 C1000 150 850 200 640 170 C420 140 240 200 0 160Z" fill="#eef1f2"/></svg>

<!-- Services -->
<div class="abs service" style="left:114px"><div class="service-ring"><div class="service-photo" role="img" aria-label="Photo of a heel with highlighted pain area" style="background:radial-gradient(circle at 60% 45%,#e4553a 0%,#ef9a6f 30%,#f1d2bd 75%)"></div></div><div class="service-label">HEEL AND ARCH PAIN</div></div>
<div class="abs service" style="left:366px"><div class="service-ring"><div class="service-photo" role="img" aria-label="Photo of toenail care treatment" style="background:linear-gradient(135deg,#f6eee7,#dcb9a0 55%,#b98f75)"></div></div><div class="service-label">SKIN AND NAIL CARE</div></div>
<div class="abs service" style="left:618px"><div class="service-ring"><div class="service-photo" role="img" aria-label="Photo of a runner holding an injured ankle" style="background:radial-gradient(circle at 45% 55%,#d93b30 0%,#e79a82 40%,#cfe0c2 90%)"></div></div><div class="service-label">SPORTS INJURIES</div></div>
<div class="abs service" style="left:870px"><div class="service-ring"><div class="service-photo" role="img" aria-label="Photo of an ankle being bandaged" style="background:linear-gradient(135deg,#fbfaf8,#e9ddd2 50%,#c9ad98)"></div></div><div class="service-label">SPORTS INJURIES</div></div>

<!-- Free book -->
<div class="abs book-band" role="img" aria-label="Faded photo of feet resting on a white surface"></div>
<h2 class="abs book-title">FREE BOOK</h2>
<div class="abs book-sub">Free Foot Surgery Book by Podiatric Surgeon, <span>Dr Dana Whitford</span></div>
<div class="abs book-desc">This book was created to demonstrate examples of some foot conditions that can be surgically corrected by our Podiatric Surgeon, Dr Whitford.</div>
<a class="abs btn book-btn">VIEW DETAILS</a>
<div class="abs book-cover">
  <div class="cover-title">Podiatric Surgery</div>
  <div class="cover-author">Dr Dana Whitford BSc, MPod, FACPS</div>
  <ul class="cover-list"><li>• Bunions and Toe Deformities</li><li>• Heel and Arch Surgery</li><li>• Recovery and Aftercare</li></ul>
  <div class="cover-photo" role="img" aria-label="Photo of a surgical team in an operating theatre"></div>
</div>

<!-- Team -->
<h2 class="abs section-title team-title">OUR TEAM</h2>
<svg class="abs team-arrow" style="left:74px" viewBox="0 0 24 40"><path d="M20 4 L6 20 L20 36" fill="none" stroke="#c3c9cd" stroke-width="4"/></svg>
<svg class="abs team-arrow" style="left:1102px" viewBox="0 0 24 40"><path d="M4 4 L18 20 L4 36" fill="none" stroke="#c3c9cd" stroke-width="4"/></svg>
<div class="abs team-card" style="left:120px"><div class="team-photo" role="img" aria-label="Portrait photo of podiatric surgeon Dana Whitford" style="background:radial-gradient(ellipse 80px 90px at 50% 45%,#e8c3a8 0%,rgba(232,195,168,0) 100%),radial-gradient(ellipse 120px 60px at 50% 100%,#8fa7b8 0%,rgba(143,167,184,0) 100%),#f3f1ee"></div><div class="team-name"><b>DANA WHITFORD</b><span>Podiatric Surgeon</span></div></div>
<div class="abs team-card" style="left:370px"><div class="team-photo" role="img" aria-label="Portrait photo of podiatrist Marcus Ellery" style="background:radial-gradient(ellipse 80px 90px at 50% 45%,#e2b79c 0%,rgba(226,183,156,0) 100%),radial-gradient(ellipse 120px 60px at 50% 100%,#e6eef2 0%,rgba(230,238,242,0) 100%),#ecebe8"></div><div class="team-name"><b>MARCUS ELLERY</b><span>Podiatrist</span></div></div>
<div class="abs team-card" style="left:620px"><div class="team-photo" role="img" aria-label="Portrait photo of podiatrist Priya Castell" style="background:radial-gradient(ellipse 80px 90px at 50% 45%,#e4b89b 0%,rgba(228,184,155,0) 100%),radial-gradient(ellipse 120px 70px at 50% 100%,#5a4436 0%,rgba(90,68,54,0) 100%),#f2f0ed"></div><div class="team-name"><b>PRIYA CASTELL</b><span>Podiatrist</span></div></div>
<div class="abs team-card" style="left:870px"><div class="team-photo" role="img" aria-label="Portrait photo of podiatrist Sophie Randell" style="background:radial-gradient(ellipse 80px 90px at 50% 45%,#efc6ab 0%,rgba(239,198,171,0) 100%),radial-gradient(ellipse 120px 70px at 50% 100%,#d8c06e 0%,rgba(216,192,110,0) 100%),#f4f2ef"></div><div class="team-name"><b>SOPHIE RANDELL</b><span>Podiatrist</span></div></div>

<!-- Partners -->
<h2 class="abs section-title partners-title">OUR PARTNERS</h2>
<div class="abs partner" style="left:110px"><i></i><b style="width:120px"></b></div>
<div class="abs partner" style="left:342px"><i></i><b style="width:100px"></b></div>
<div class="abs partner" style="left:546px"><b style="width:130px"></b></div>
<div class="abs partner" style="left:748px"><b style="width:128px"></b></div>
<div class="abs partner" style="left:946px"><i style="border-radius:4px"></i><b style="width:104px"></b></div>

<!-- Contact -->
<svg class="abs contact-wave" viewBox="0 0 1200 600" preserveAspectRatio="none">
  <path d="M0 70 C180 10 360 120 600 80 C840 40 1000 0 1200 40 L1200 600 L0 600Z" fill="#1588b3"/>
  <path d="M0 110 C220 50 420 150 640 110 C860 70 1020 40 1200 80 L1200 600 L0 600Z" fill="#0f77a0"/>
</svg>
<div class="abs subscribe"><div class="subscribe-input">Enter Your Email</div><div class="subscribe-btn">SUBSCRIBE</div></div>
<div class="abs contact-title">CONTACT US</div>
<div class="abs contact-line" style="top:3608px"><svg width="16" height="22" viewBox="0 0 16 22"><path d="M8 0a8 8 0 00-8 8c0 6 8 14 8 14s8-8 8-14a8 8 0 00-8-8zm0 11a3 3 0 110-6 3 3 0 010 6z" fill="#ffffff"/></svg><span>14 Marlowe Street Ferndale,<br>WA 6148</span></div>
<div class="abs contact-line" style="top:3660px;font-weight:700;font-size:16px"><svg width="18" height="18" viewBox="0 0 24 24"><path d="M6.6 10.8a15 15 0 006.6 6.6l2.2-2.2a1 1 0 011-.25 11.4 11.4 0 003.6.57 1 1 0 011 1V20a1 1 0 01-1 1A17 17 0 013 4a1 1 0 011-1h3.5a1 1 0 011 1 11.4 11.4 0 00.57 3.6 1 1 0 01-.25 1z" fill="#ffffff"/></svg><span>Call Us (08) 9000 4127</span></div>
<div class="abs contact-brand"><span class="brand-dot"></span><span class="brand-name">Kelvale Heel Care Clinic</span></div>
<div class="abs appt">
  <h3>REQUEST AN APPOINTMENT</h3>
  <div class="appt-grid">
    <div class="field">Name</div><div class="field">Email</div>
    <div class="field">Contact</div><div class="field">Subject</div>
    <div class="field area">Content</div>
    <div class="appt-submit">SUBMIT</div>
  </div>
</div>

<!-- Map -->
<div class="abs map" role="img" aria-label="Street map showing the clinic location near the river"></div>
<div class="abs map-toggle"><span>Map</span><span>Satellite</span></div>
<div class="abs map-card" style="top:3900px;z-index:1"><b>Ferndale Office</b><br>14 Marlowe Street<br>Ferndale, WA 6148<br>(08) 9000 4127</div>
<svg class="abs" style="left:588px;top:4104px" width="26" height="38" viewBox="0 0 16 22"><path d="M8 0a8 8 0 00-8 8c0 6 8 14 8 14s8-8 8-14a8 8 0 00-8-8zm0 11a3 3 0 110-6 3 3 0 010 6z" fill="#e0453a"/></svg>

<!-- Footer -->
<footer class="abs site-footer"></footer>
<div class="abs footer-social"><span></span><span></span><span></span><span></span></div>
<div class="abs copyright">© 2017 Kelvale Heel Care Clinic. All Rights Reserved. Website built with care · Privacy Policy</div>

</body>
</html>
```